Heritage Hollow Business Cards

Require a business card design. <br/><br/>Needs to include logo (either round or long version) plus these details:<br/>Maya Torvell<br/>Heritage Hollow<br/>maya@kelvadtrading.com.au<br/>02 6481 7395<br/>PO Box Glenwarra NSW 2791<br/>www.heritagehollow.com.au<br/><br/>I need in an editable format so that I can create for multiple staff members. <br/><br/>

Target Market(s)

We are an online store selling renovation products to home owners are builders. Looking for a classic classy design.

Industry/Entity Type

Home And Garden

Contact Information for Business Card

Maya Torvell
Heritage Hollow
maya@kelvadtrading.com.au
02 6481 7395
PO Box Glenwarra NSW 2791
www.heritagehollow.com.au

Colors

Designer to choose colors to be used in the design.

Requirements
Must have
• Must include Logo.

```html
<!DOCTYPE html>
<html lang="en">
<head>
<meta charset="utf-8">
<title>Heritage Hollow Business Cards</title>
<link rel="stylesheet" href="https://fonts.googleapis.com/css2?family=Lora:wght@500&family=Open+Sans:wght@400;600&display=swap">
<style>
  :root {
    --page: #5a5a5a;
    --card: #1e1d1e;
    --ink: #ffffff;
    --ink-soft: #e6e6e6;
    --rule: #bdbdbd;
    --emboss-a: #2b2a2b;
    --emboss-b: #111011;
    --arc: #8a8a8a;
  }
  * { box-sizing: border-box; margin: 0; padding: 0; }
  html, body { width: 1200px; height: 1124px; overflow: hidden; background: var(--page); }
  .sheet {
    width: 1200px; height: 1124px;
    display: flex; flex-direction: column; align-items: center; justify-content: center; gap: 40px;
  }
  .card {
    position: relative; width: 900px; height: 514px;
    background: var(--card); overflow: hidden;
    box-shadow: 0 10px 24px rgba(0,0,0,.35);
  }
  /* front */
  .card-front .arc-art { position: absolute; inset: 0; }
  .card-front .brand-name {
    position: absolute; left: 600px; top: 196px;
    font-family: "Lora", Georgia, serif; font-weight: 500; font-size: 34px;
    color: var(--ink); letter-spacing: .3px;
  }
  /* back */
  .card-back .logo-lockup {
    position: absolute; left: 70px; top: 228px;
    display: flex; align-items: center; gap: 16px;
  }
  .logo-lockup .mark-dot {
    width: 34px; height: 34px; border: 2px solid var(--ink); border-radius: 50%;
  }
  .logo-lockup .logo-name {
    font-family: "Lora", Georgia, serif; font-weight: 500; font-size: 36px; color: var(--ink);
  }
  .card-back .divider {
    position: absolute; left: 420px; top: 120px; width: 2px; height: 290px; background: var(--rule);
  }
  .contact {
    position: absolute; left: 462px; top: 120px;
    font-family: "Open Sans", Arial, sans-serif; color: var(--ink-soft);
  }
  .contact .person { font-weight: 600; font-size: 30px; color: var(--ink); line-height: 1.1; }
  .contact .company { font-size: 21px; margin-top: 2px; }
  .contact .address { font-size: 21px; line-height: 1.3; margin-top: 22px; }
  .contact .lines { list-style: none; margin-top: 20px; }
  .contact .lines li { display: flex; align-items: center; gap: 14px; font-size: 21px; line-height: 1.5; }
  .contact .lines svg { width: 18px; height: 18px; flex: none; }
</style>
</head>
<body>
<main class="sheet">
  <section class="card card-front">
    <svg class="arc-art" width="900" height="514" viewBox="0 0 900 514">
      <defs>
        <linearGradient id="embossFill" x1="0" y1="0" x2="1" y2="1">
          <stop offset="0" stop-color="var(--emboss-a)"/>
          <stop offset="1" stop-color="var(--emboss-b)"/>
        </linearGradient>
        <clipPath id="arcClip"><circle cx="330" cy="600" r="380"/></clipPath>
      </defs>
      <rect role="img" aria-label="Embossed sketch of a heritage house roof with chimney" x="0" y="220" width="600" height="294" fill="url(#embossFill)" clip-path="url(#arcClip)"/>
      <circle cx="330" cy="600" r="380" fill="none" stroke="var(--arc)" stroke-width="2"/>
      <line x1="430" y1="256" x2="600" y2="256" stroke="var(--arc)" stroke-width="1.5"/>
    </svg>
    <div class="brand-name">Heritage Hollow</div>
  </section>

  <section class="card card-back">
    <div class="logo-lockup">
      <span class="mark-dot"></span>
      <span class="logo-name">Heritage Hollow</span>
    </div>
    <div class="divider"></div>
    <div class="contact">
      <p class="person">Maya Torvell</p>
      <p class="company">Heritage Hollow</p>
      <p class="address">PO Box Glenwarra<br>NSW 2791</p>
      <ul class="lines">
        <li>
          <svg viewBox="0 0 24 24" fill="#fff"><path d="M6.6 10.8a15.1 15.1 0 0 0 6.6 6.6l2.2-2.2c.3-.3.7-.4 1-.2 1.1.4 2.3.6 3.6.6.6 0 1 .4 1 1V20c0 .6-.4 1-1 1A17 17 0 0 1 3 4c0-.6.4-1 1-1h3.5c.6 0 1 .4 1 1 0 1.3.2 2.5.6 3.6.1.3 0 .7-.2 1z"/></svg>
          <span>02 6481 7395</span>
        </li>
        <li>
          <svg viewBox="0 0 24 24" fill="none" stroke="#fff" stroke-width="2"><rect x="3" y="5" width="18" height="14" rx="1"/><path d="M3 6l9 7 9-7"/></svg>
          <span>maya@kelvadtrading.com.au</span>
        </li>
        <li>
          <svg viewBox="0 0 24 24" fill="none" stroke="#fff" stroke-width="1.8"><circle cx="12" cy="12" r="9"/><path d="M3 12h18M12 3c3 3 3 15 0 18M12 3c-3 3-3 15 0 18"/></svg>
          <span>www.heritagehollow.com.au</span>
        </li>
      </ul>
    </div>
  </section>
</main>
</body>
</html>
```